Banner 170x60 for Barrel Sauna Rental Banner

Attention, please do every side graphic distance 5cm . It is for attachment.
search for a graphic design in dimension 170x60cm.
we have a barrel sauna rental service and need a banner for the two sides.
please look photos.
big text is: (I CAN RENT ME!!! )in english like: you can rent me
heisse-holzstube.de
015243197720
info@heisse-holzstube.de
we need an eye catcher design!!!!
Design:
maybe wood in at background.
maybe burning fire and sauna style.
Please don't use my barrell sauna pictures. It is only an example for you what we do. The barrel sauna is on build at the moment.

```html
<!DOCTYPE html>
<html lang="en">
<head>
<meta charset="utf-8">
<title>Barrel Sauna Rental Banner</title>
<link rel="stylesheet" href="https://fonts.googleapis.com/css2?family=Montserrat:ital,wght@0,300;0,400;0,600;0,700;0,800;0,900;1,500&display=swap">
<style>
  :root {
    --page: #ffffff;
    --wood-dark: #3a1a0e;
    --wood-mid: #5a2c17;
    --wood-light: #7a4226;
    --headline: #d2ff1c;
    --headline-edge: #1a0d06;
    --booking: #f4ef1a;
    --white: #ffffff;
    --pill: rgba(120, 78, 52, 0.85);
    --photo-warm: #d9a062;
    --photo-deep: #a8632c;
  }
  * { margin: 0; padding: 0; box-sizing: border-box; }
  html, body {
    width: 1200px; height: 1200px; overflow: hidden;
    background: var(--page);
    font-family: "Montserrat", sans-serif;
  }
  .canvas { position: relative; width: 1200px; height: 1200px; }
  .banner {
    position: absolute; left: 65px; top: 142px;
    width: 1070px; height: 378px; overflow: hidden;
  }
  .banner__wood {
    position: absolute; inset: 0;
    background:
      linear-gradient(90deg, rgba(0,0,0,0.18) 0 2%, transparent 2% 12%, rgba(0,0,0,0.15) 12% 13%, transparent 13% 31%, rgba(0,0,0,0.15) 31% 32%, transparent 32% 52%, rgba(0,0,0,0.15) 52% 53%, transparent 53% 74%, rgba(0,0,0,0.15) 74% 75%, transparent 75%),
      linear-gradient(100deg, var(--wood-mid), var(--wood-dark) 30%, var(--wood-light) 55%, var(--wood-dark) 80%, var(--wood-mid));
  }
  .photo {
    position: absolute; border-radius: 50%;
    border: 3px solid var(--white);
    box-shadow: 0 2px 6px rgba(0,0,0,0.5);
  }
  .photo--interior {
    left: 46px; top: 60px; width: 192px; height: 192px;
    background: radial-gradient(circle at 45% 45%, var(--photo-warm), var(--photo-deep));
  }
  .photo--cabin {
    left: 193px; top: 167px; width: 120px; height: 120px;
    background: radial-gradient(circle at 50% 40%, #e6b076, #b0692e);
  }
  .brand {
    position: absolute; left: 100px; top: 288px; width: 130px;
    display: flex; align-items: center; gap: 6px;
    color: var(--white); font-weight: 700; font-size: 11px; letter-spacing: 0.3px;
  }
  .brand__mark { width: 10px; height: 10px; border-radius: 50%; background: var(--white); flex: none; }
  .headline {
    position: absolute; left: 250px; top: 70px; width: 780px;
    text-align: center; font-weight: 800; font-size: 68px; line-height: 1;
    color: var(--headline); letter-spacing: -0.5px;
    -webkit-text-stroke: 3px var(--headline-edge); paint-order: stroke fill;
    text-shadow: 3px 4px 0 var(--headline-edge);
  }
  .booking {
    position: absolute; left: 440px; top: 168px; width: 400px;
    text-align: center; font-weight: 400; font-size: 26px; color: var(--booking);
  }
  .phone {
    position: absolute; left: 390px; top: 200px; width: 500px;
    text-align: center; font-weight: 600; font-size: 54px; color: var(--white); letter-spacing: 1px;
  }
  .contacts {
    position: absolute; left: 348px; top: 282px; width: 586px; height: 32px;
    background: var(--pill); border-radius: 5px;
    display: flex; align-items: center; justify-content: space-around;
    color: var(--white); font-style: italic; font-weight: 500; font-size: 18px;
  }
  .contacts__item { display: flex; align-items: center; gap: 10px; }
  .contacts__icon { width: 18px; height: 18px; }
</style>
</head>
<body>
<main class="canvas">
  <section class="banner">
    <div class="banner__wood" role="img" aria-label="Dark brown wood grain texture background"></div>
    <div class="photo photo--interior" role="img" aria-label="Round photo of a warm wooden barrel sauna interior with stove"></div>
    <div class="photo photo--cabin" role="img" aria-label="Round photo of a wooden sauna cabin with glass door"></div>
    <div class="brand"><span class="brand__mark"></span>HEISSE-HOLZSTUBE</div>
    <h1 class="headline">YOU CAN RENT ME!</h1>
    <p class="booking">BOOKING NOW!</p>
    <p class="phone">015243197720</p>
    <div class="contacts">
      <span class="contacts__item">
        <svg class="contacts__icon" viewBox="0 0 20 20" fill="none" stroke="#fff" stroke-width="1.8"><circle cx="10" cy="10" r="8"/><ellipse cx="10" cy="10" rx="3.5" ry="8"/><line x1="2" y1="10" x2="18" y2="10"/></svg>
        heisse-holzstube.de
      </span>
      <span class="contacts__item">
        <svg class="contacts__icon" viewBox="0 0 20 20"><rect x="1" y="4" width="18" height="13" rx="1.5" fill="#fff"/><path d="M2 5 L10 11 L18 5" fill="none" stroke="#6b4430" stroke-width="1.8"/></svg>
        info@heisse-holzstube.de
      </span>
    </div>
  </section>
</main>
</body>
</html>
```